Commercial Real Estate

We need a business card design for a new commercial real estate business that specializes in apartment building brokerage. Not individual units but the entire complex. We find and represent the owners existing buildings and well as new buyers for those buildings. The design should convey trust, integrity, knowledge and growth. It should be easily read.

Target Market(s)

40 to 65 years old

Industry/Entity Type

Real Estate

```html
<!DOCTYPE html>
<html lang="en">
<head>
<meta charset="utf-8">
<title>Keystead Property Investments – Business Card</title>
<link rel="stylesheet" href="https://fonts.googleapis.com/css2?family=Bitter:wght@400;700&family=Archivo+Narrow:wght@700&display=swap">
<style>
  :root {
    --stage: #3d3e3f;
    --card-white: #ffffff;
    --teal: #6cc9c9;
    --teal-deep: #5bbcbc;
    --slate: #4a5a5a;
    --band-top: #4b5d5e;
    --band-bottom: #1f2a2b;
    --ink: #253a3b;
  }
  * { margin: 0; padding: 0; box-sizing: border-box; }
  html, body {
    width: 1200px;
    height: 900px;
    overflow: hidden;
  }
  body {
    background: var(--stage);
    display: flex;
    align-items: center;
    justify-content: center;
  }
  .business-card {
    width: 436px;
    height: 762px;
    border-radius: 38px;
    overflow: hidden;
    background: var(--teal);
    display: flex;
    flex-direction: column;
    font-family: "Bitter", Georgia, serif;
  }
  .brand-panel {
    height: 460px;
    background: var(--card-white);
    display: flex;
    flex-direction: column;
    align-items: center;
    justify-content: center;
  }
  .brand-name {
    font-family: "Bitter", Georgia, serif;
    font-weight: 400;
    font-size: 52px;
    letter-spacing: 3px;
    color: var(--slate);
    line-height: 1;
  }
  .brand-rule {
    width: 270px;
    height: 2px;
    background: var(--teal);
    margin: 14px 0 8px;
  }
  .brand-tagline {
    font-family: "Archivo Narrow", "Arial Narrow", sans-serif;
    font-weight: 700;
    font-size: 17px;
    letter-spacing: 4.2px;
    color: var(--slate);
  }
  .name-band {
    height: 35px;
    background: linear-gradient(var(--band-top), var(--band-bottom));
    border-bottom: 2px solid var(--teal-deep);
    display: flex;
    align-items: center;
    justify-content: center;
  }
  .person-name {
    font-weight: 700;
    font-size: 26px;
    color: var(--teal);
    letter-spacing: 0.5px;
    line-height: 1;
  }
  .contact-panel {
    flex: 1;
    text-align: center;
    color: var(--ink);
    font-size: 21px;
    line-height: 30px;
    padding-top: 2px;
  }
  .person-role { margin-bottom: 32px; }
  .address { margin-bottom: 26px; }
  .contact-lines { font-size: 21px; }
  .contact-lines .phone { font-family: "Archivo Narrow", Arial, sans-serif; font-weight: 400; }
  .website { font-weight: 700; }
</style>
</head>
<body>
  <article class="business-card">
    <header class="brand-panel">
      <div class="brand-name">KEYSTEAD</div>
      <div class="brand-rule"></div>
      <div class="brand-tagline">Property Investments</div>
    </header>
    <div class="name-band">
      <h1 class="person-name">ALAN MARSH</h1>
    </div>
    <section class="contact-panel">
      <p class="person-role">Managing Director</p>
      <p class="address">Address, Land dummy<br>dummy dummy City</p>
      <p class="contact-lines">
        <span class="phone">00 00 00 00 00</span><br>
        alan@keystead.com<br>
        <span class="website">www.keystead.com</span>
      </p>
    </section>
  </article>
</body>
</html>
```